Custom t-shirts and merchandise orders t shirts and merchendise

I'd like to build a webpage to promote clothing apparel merchandise and also print on demand. A copy of my logo is attached! An example webpage for the print on demand would be brelvantops.com, Kelpwickgarb.com, and quornstamps.com. If possible, I'd like the web page colors to match the attached logo but it is not absolutely necessary.

Target Market(s)

Vidlorn, Kinmarsh, and zentrip viewers age 20-35

Industry/Entity Type

Apparel Store

Logo Text

TaroPeaks

Coding

Coded - Design and coding required

Number of Pages Required

5+ page

Font styles to use
Sans Serif

Requirements
Must have
• Print on demand page to custom build a shirt design.
Nice to have
• Subscribe option

```html
<!DOCTYPE html>
<html lang="en">
<head>
<meta charset="utf-8">
<title>TaroPeaks — Custom Apparel</title>
<link rel="stylesheet" href="https://fonts.googleapis.com/css2?family=Kanit:wght@600;700&family=Source+Sans+3:wght@400;600;700&display=swap">
<style>
:root{
  --blue:#1f8ee8;
  --pink:#e3077f;
  --orange:#ef6e1f;
  --ink:#111;
  --text:#333;
  --muted:#666;
  --line:#dcdcdc;
  --green:#2fc44a;
  --white:#fff;
}
*{box-sizing:border-box;margin:0;padding:0}
html,body{width:1200px;height:4277px;overflow:hidden}
body{position:relative;font-family:"Source Sans 3",sans-serif;color:var(--text);background:var(--white)}
.abs{position:absolute}
.heading{font-family:"Kanit",sans-serif;font-weight:700;color:var(--ink);text-transform:uppercase;text-align:center}
.btn{position:absolute;display:flex;align-items:center;justify-content:center;background:var(--pink);color:var(--white);font-weight:700;border-radius:30px}

.topbar{left:0;top:0;width:1200px;height:40px;background:var(--blue);color:var(--white);font-size:14px}
.topbar span{position:absolute;top:11px}
.header{left:0;top:40px;width:1200px;height:76px;background:var(--white)}
.brand{position:absolute;font-family:"Source Sans 3",sans-serif;font-weight:700;color:var(--ink)}
.nav{left:0;top:116px;width:1200px;height:45px;background:linear-gradient(#fafafa,#e6e6e6);font-size:17px;color:#222}
.nav span{position:absolute;top:11px}
.nav .active{color:var(--blue)}

.hero{left:0;top:161px;width:1200px;height:689px}
.hero h1{position:absolute;left:90px;top:145px;font-family:"Kanit",sans-serif;font-size:62px;color:var(--white);line-height:1}
.hero p{position:absolute;left:91px;top:225px;font-size:25px;font-weight:700;color:var(--white)}
.dots{position:absolute;left:88px;top:478px;display:flex;gap:7px}
.dots i{width:9px;height:9px;border-radius:50%;background:var(--white)}
.dots i:first-child{background:var(--blue)}

.card{position:absolute;top:1004px;width:250px;text-align:center}
.card .shot{height:357px;position:relative}
.card .tag{position:absolute;top:14px;width:26px;height:11px;font-size:7px;color:var(--white);display:flex;align-items:center;justify-content:center}
.card h3{margin-top:15px;font-size:19px;font-weight:700;color:#222}
.card p{font-size:17px;color:#444}

.form-label{font-size:15px;color:#333}
.text-block{font-size:15px;line-height:29.5px;color:#444}

.brand-box{position:absolute;top:3464px;width:186px;height:108px;border:2px solid var(--line);display:flex;align-items:center;justify-content:center;font-size:26px;font-weight:700;color:#b5b5b5}

.footer{left:0;top:3660px;width:1200px;height:617px}
.contact-col{position:absolute;top:4020px;width:340px;text-align:center;color:var(--white)}
.contact-col h4{margin-top:18px;font-size:21px;font-weight:700}
.contact-col p{margin-top:14px;font-size:14px;line-height:22px}
.social{position:absolute;top:3860px;width:32px;height:32px;background:var(--pink);border-radius:3px}
.card-chip{position:absolute;top:3868px;width:30px;height:18px;border-radius:2px}
.legal{position:absolute;top:4228px;font-size:13px;color:var(--white)}
</style>
</head>
<body>

<div class="abs topbar">
  <svg class="abs" style="left:94px;top:11px" width="13" height="18" viewBox="0 0 13 18"><path d="M6.5 0C2.9 0 0 2.8 0 6.4 0 11 6.5 18 6.5 18S13 11 13 6.4C13 2.8 10.1 0 6.5 0zm0 9a2.6 2.6 0 110-5.2 2.6 2.6 0 010 5.2z" fill="#fff"/></svg>
  <span style="left:117px">418 Orrin Lane • Dellmoor, Tavoria 40217</span>
  <span style="left:848px">En</span>
  <svg class="abs" style="left:876px;top:16px" width="10" height="6"><path d="M1 1l4 4 4-4" stroke="#fff" fill="none" stroke-width="1.5"/></svg>
  <span style="left:918px;top:6px;font-size:20px">|</span>
  <svg class="abs" style="left:955px;top:13px" width="17" height="13"><rect x="1" y="1" width="15" height="11" rx="1" fill="none" stroke="#fff" stroke-width="1.5"/><path d="M1 1l7.5 6L16 1" fill="none" stroke="#fff" stroke-width="1.5"/></svg>
  <span style="left:984px">hello@taropeaks.shop</span>
</div>

<div class="abs header">
  <div class="brand" style="left:90px;top:22px;font-size:30px">TaroPeaks</div>
  <div class="btn" style="left:514px;top:18px;width:164px;height:44px;font-size:16px">Design Now</div>
  <svg class="abs" style="left:730px;top:30px" width="18" height="16"><path d="M0 1h3l2.5 9h9l2-6H5" fill="none" stroke="#3b8de0" stroke-width="1.6"/><circle cx="7" cy="13.5" r="1.5" fill="#3b8de0"/><circle cx="13" cy="13.5" r="1.5" fill="#3b8de0"/></svg>
  <div class="abs" style="left:754px;top:30px;font-size:15px;color:#777">Cart has Empty</div>
  <svg class="abs" style="left:918px;top:17px" width="44" height="44"><circle cx="22" cy="22" r="20.5" fill="none" stroke="var(--blue)" stroke-width="2"/><path d="M16 14c-1 1-1 3 0 5 2 4 5 7 9 9 2 1 4 1 5 0l-3-4-2 1c-2-1-4-3-5-5l1-2z" fill="var(--blue)"/></svg>
  <div class="abs" style="left:977px;top:25px;font-size:22px;font-weight:700;color:var(--blue)">555.014.2290</div>
</div>

<div class="abs nav">
  <span class="active" style="left:98px">Home</span>
  <span style="left:214px">About</span>
  <span style="left:332px">Products</span>
  <span style="left:472px">What We Do</span>
  <span style="left:638px">Latest Blog</span>
  <span style="left:797px">News</span>
  <span style="left:909px">Gallery</span>
  <span style="left:1034px">Contact</span>
</div>

<section class="abs hero">
  <svg class="abs" style="left:0;top:0" width="1200" height="689" viewBox="0 0 1200 689">
    <defs><linearGradient id="heroBg" x1="0" x2="1"><stop offset="0" stop-color="#e8601a"/><stop offset=".6" stop-color="#f07a28"/><stop offset="1" stop-color="#ec6a1d"/></linearGradient></defs>
    <path d="M0 0H1200V570L600 689 0 570z" fill="var(--pink)"/>
    <path d="M0 0H1200V555L600 672 0 570z" fill="url(#heroBg)"/>
  </svg>
  <div class="abs" role="img" aria-label="Model wearing a white printed t-shirt" style="left:540px;top:0;width:340px;height:600px;background:radial-gradient(ellipse at 50% 55%,rgba(250,232,218,.55) 0,rgba(246,160,100,.25) 55%,rgba(240,122,40,0) 80%)"></div>
  <h1>TaroPeaks</h1>
  <p>Because Every Print Has a Story</p>
  <div class="btn" style="left:90px;top:316px;width:161px;height:52px;font-size:16px">Buy Now</div>
  <div class="dots"><i></i><i></i><i></i><i></i></div>
</section>

<h2 class="abs heading" style="left:0;top:930px;width:1200px;font-size:38px">Featured Products</h2>
<div class="card" style="left:75px">
  <div class="shot" role="img" aria-label="White t-shirt on wooden background" style="background:linear-gradient(135deg,#8a5634,#c9b3a2 50%,#8a5634)"><span class="tag" style="left:14px;background:#e01e2b">-20%</span><span class="tag" style="right:14px;background:#222">New</span></div>
  <h3>Product Name</h3><p>$ 106.59</p>
</div>
<div class="card" style="left:342px">
  <div class="shot" role="img" aria-label="Black t-shirt with text print on teal marble" style="background:linear-gradient(135deg,#2a7f8a,#1a2a2e 50%,#3a6f6a)"><span class="tag" style="right:14px;background:#222">New</span></div>
  <h3>Product Name</h3><p>$ 106.59</p>
</div>
<div class="card" style="left:608px">
  <div class="shot" role="img" aria-label="Grey t-shirt with photo print" style="background:linear-gradient(#9a9a9a,#8c8c8c)">
    <span class="tag" style="left:14px;background:#e01e2b">-20%</span>
    <svg class="abs" style="left:112px;top:160px" width="34" height="34"><circle cx="15" cy="15" r="11" fill="none" stroke="#fff" stroke-width="2"/><path d="M15 9v12M9 15h12M23 23l8 8" stroke="#fff" stroke-width="2"/></svg>
    <div class="abs" style="left:27px;top:294px;width:196px;height:27px;background:#1e9be8;color:#fff;font-size:13px;font-weight:700;display:flex;align-items:center;justify-content:center">Customized Your Design</div>
  </div>
  <h3>Product Name</h3><p>$ 106.59</p>
</div>
<div class="card" style="left:875px">
  <div class="shot" role="img" aria-label="Black t-shirt with sports print on wood" style="background:linear-gradient(135deg,#6e4a2e,#241c16 50%,#6e4a2e)"><span class="tag" style="left:14px;background:#e01e2b">-20%</span><span class="tag" style="right:14px;background:#222">New</span></div>
  <h3>Product Name</h3><p>$ 106.59</p>
</div>

<section class="abs" style="left:0;top:1511px;width:1200px;height:517px">
  <div class="abs" role="img" aria-label="Man in sunglasses wearing a white logo t-shirt in a street" style="left:0;top:0;width:1200px;height:517px;background:linear-gradient(90deg,#a8aaac 0,#cfcac3 40%,#dcd6ce 65%,#8a7662 100%)"></div>
  <h2 class="abs heading" style="left:90px;top:118px;font-size:38px;text-align:left">About Us</h2>
  <p class="abs" style="left:88px;top:185px;width:490px;font-size:16.5px;line-height:29.5px;color:#222">Lorem ipsum dolor sit amet, consectetur adipiscing elit, sed do eiusmod tempor incididunt ut labore et dolore magna aliqua. Ut enim ad minim veniam, quis nostrud exercitation ullamco laboris nisi ut aliquip ex ea commodo consequat.</p>
  <div class="btn" style="left:90px;top:334px;width:166px;height:56px;font-size:16px">Shop Now</div>
</section>

<h2 class="abs heading" style="left:0;top:2105px;width:1190px;font-size:38px">Customized Your Design</h2>
<p class="abs" style="left:330px;top:2168px;width:530px;text-align:center;font-size:16px;line-height:26px;color:#333">Lorem ipsum dolor sit amet, consectetur adipiscing elit, sed do eiusmod tempor incididunt ut labore et dolore magna aliqua.</p>
<div class="abs" role="img" aria-label="Woman wearing a custom printed white t-shirt" style="left:86px;top:2243px;width:472px;height:451px;background:linear-gradient(#f9b732,#f4a623)"></div>
<div class="abs form-label" style="left:591px;top:2254px">No Of Quantity :</div>
<div class="abs" style="left:719px;top:2243px;width:390px;height:38px;border:1px solid var(--line);font-size:14px;color:#666;padding:9px 14px">1</div>
<svg class="abs" style="left:1086px;top:2259px" width="10" height="6"><path d="M1 1l4 4 4-4" stroke="#777" fill="none" stroke-width="1.4"/></svg>
<div class="abs" style="left:591px;top:2299px;width:518px;height:130px;border:1px solid var(--line);display:flex;align-items:center;justify-content:center;font-size:15px;color:#999;gap:8px">
  <svg width="16" height="14"><path d="M8 1v9M4 5l4-4 4 4M1 10v3h14v-3" stroke="#999" fill="none" stroke-width="1.6"/></svg>Upload Your Logo or Images
</div>
<div class="abs form-label" style="left:591px;top:2452px">Color :</div>
<svg class="abs" style="left:655px;top:2449px" width="180" height="26">
  <circle cx="12" cy="13" r="11" fill="#cfcfcf"/><circle cx="48" cy="13" r="11" fill="#000"/><circle cx="84" cy="13" r="10.5" fill="#fff" stroke="#ddd"/><circle cx="120" cy="13" r="11" fill="#ee1111"/><circle cx="156" cy="13" r="11" fill="#2355dd"/>
</svg>
<p class="abs text-block" style="left:591px;top:2485px;width:525px">Lorem ipsum dolor sit amet, consectetur adipiscing elit, sed do eiusmod tempor incididunt ut labore et dolore magna aliqua. Ut enim ad minim veniam, quis nostrud exercitation ullamco laboris nisi ut aliquip ex ea commodo consequat. Duis aute irure dolor in reprehenderit in voluptate velit esse cillum dolore eu fugiat nulla pariatur.</p>
<div class="btn" style="left:591px;top:2649px;width:518px;height:45px;font-size:16px">Buy Now</div>

<section class="abs" style="left:0;top:2789px;width:1200px;height:518px">
  <div class="abs" role="img" aria-label="Person in a white logo t-shirt against a weathered wall" style="left:0;top:0;width:1200px;height:518px;background:linear-gradient(90deg,#c4c4c4,#e4e2df 40%,#e6e3df 70%,#cfccc8)"></div>
  <h2 class="abs" style="left:750px;top:120px;width:360px;text-align:center;font-family:Kanit,sans-serif;font-size:36px;color:#111">Testimonials</h2>
  <p class="abs" style="left:760px;top:186px;width:340px;text-align:center;font-size:16px;line-height:35px;color:#333">Lorem ipsum dolor sit amet, consectetur adipiscing elit, sed do eiusmod tempor incididunt ut labore et dolore magna aliqua.</p>
  <div class="btn" style="left:835px;top:320px;width:190px;height:58px;font-size:16px">Read More</div>
</section>

<h2 class="abs heading" style="left:0;top:3380px;width:1200px;font-size:38px">Our Brands</h2>
<svg class="abs" style="left:65px;top:3508px" width="38" height="20"><path d="M37 10H3M11 2L2 10l9 8" stroke="#222" fill="none" stroke-width="2.5"/></svg>
<div class="brand-box" style="left:110px">Brenwick</div>
<div class="brand-box" style="left:309px">Morrowell</div>
<div class="brand-box" style="left:508px">Quillon</div>
<div class="brand-box" style="left:707px;background:#f2f2f2">Varnet</div>
<div class="brand-box" style="left:906px">Lintora</div>
<svg class="abs" style="left:1098px;top:3508px" width="38" height="20"><path d="M1 10h34M27 2l9 8-9 8" stroke="#222" fill="none" stroke-width="2.5"/></svg>

<footer class="abs footer">
  <svg class="abs" style="left:0;top:0" width="1200" height="617" viewBox="0 0 1200 617">
    <path d="M0 125L600 9 1200 125z" fill="var(--green)"/>
    <path d="M0 130L600 18 1200 130V617H0z" fill="#000"/>
  </svg>
</footer>
<div class="card-chip" style="left:88px;background:#1b4fb3"></div>
<div class="card-chip" style="left:130px;background:#f29a1a"></div>
<div class="card-chip" style="left:172px;background:#e8e8e8"></div>
<div class="card-chip" style="left:214px;background:#2a5ad6"></div>
<div class="social" style="left:896px"></div>
<div class="social" style="left:941px"></div>
<div class="social" style="left:986px"></div>
<div class="social" style="left:1031px"></div>
<div class="social" style="left:1076px"></div>
<div class="abs" style="left:0;top:3870px;width:1200px;text-align:center;display:flex;justify-content:center;align-items:center;gap:12px">
  <span style="width:18px;height:18px;border-radius:50%;background:var(--pink);display:inline-block"></span>
  <span class="brand" style="position:static;color:#fff;font-size:46px">TaroPeaks</span>
</div>
<h2 class="abs heading" style="left:0;top:3940px;width:1200px;font-size:33px;color:#fff">Contact Informations</h2>
<div class="abs" style="left:413px;top:4026px;width:1px;height:130px;background:#333"></div>
<div class="abs" style="left:767px;top:4026px;width:1px;height:130px;background:#333"></div>
<div class="contact-col" style="left:72px">
  <svg width="22" height="22" viewBox="0 0 22 22"><path d="M4 2c-2 2-2 5 0 9 2 4 5 7 9 9 3 1 5 0 6-1l-3-5-3 1c-2-1-4-3-5-6l2-2z" fill="#fff"/></svg>
  <h4>CALL US</h4><p>(+100)5 550 1200<br>(+100)5 550 1200</p>
</div>
<div class="contact-col" style="left:430px">
  <svg width="24" height="22" viewBox="0 0 24 22"><path d="M12 1L1 11h3v10h6v-6h4v6h6V11h3z" fill="#fff"/></svg>
  <h4>FIND US</h4><p>418 Orrin Lane • Dellmoor,<br>Tavoria 40217</p>
</div>
<div class="contact-col" style="left:787px">
  <svg width="26" height="20" viewBox="0 0 26 20"><rect x="0" y="0" width="26" height="20" rx="2" fill="#fff"/><path d="M1 2l12 9 12-9" stroke="#000" fill="none" stroke-width="2"/></svg>
  <h4>EMAIL</h4><p>info@taropeaks.shop<br>help@taropeaks.shop</p>
</div>
<div class="abs" style="left:88px;top:4200px;width:1040px;height:1px;background:#333"></div>
<div class="legal" style="left:88px">TaroPeaks Apparel © 2021. All Rights Reserved.</div>
<div class="legal" style="left:662px">About</div>
<div class="legal" style="left:720px">Legal information</div>
<div class="legal" style="left:843px">Contact</div>
<div class="legal" style="left:912px">Term of service</div>
<div class="legal" style="left:1025px">Privacy policy</div>
<div class="legal" style="left:1141px">C28</div>

</body>
</html>
```